holloway paving service

Needs to have phone number 0418259730 and email markholloway@brightmail.com.au.
ABN 62318470915
name mark holloway

For all your concreting solutions
Excavation
Exposed & colour concrete
House & shed slabs
Driveways
Landing & steps

Contact Information for Business Card

ph 0418259730
email markholloway@brightmail.com.au.
ABN 62318470915
name mark holloway

```html
<!DOCTYPE html>
<html lang="en">
<head>
<meta charset="utf-8">
<title>Holloway Paving Service – Business Card</title>
<link rel="stylesheet" href="https://fonts.googleapis.com/css2?family=Lato:wght@400;700&family=Oswald:wght@500&display=swap">
<style>
  :root {
    --backdrop: #2b2b2c;
    --card: #1c1c1d;
    --card-edge: #252526;
    --ink: #f2f2f2;
    --ink-soft: #b9b9b9;
    --accent: #f26a21;
  }
  * { box-sizing: border-box; margin: 0; padding: 0; }
  html, body { width: 1200px; height: 900px; overflow: hidden; }
  body {
    background: var(--backdrop);
    font-family: "Lato", Arial, sans-serif;
    color: var(--ink);
    display: flex;
    flex-direction: column;
    align-items: center;
    justify-content: center;
    gap: 40px;
  }
  .card {
    position: relative;
    width: 640px;
    height: 366px;
    background: linear-gradient(135deg, var(--card) 0%, var(--card-edge) 100%);
    box-shadow: 0 8px 24px rgba(0,0,0,0.45);
    overflow: hidden;
  }

  /* Front */
  .brand {
    position: absolute;
    left: 0; right: 0; top: 118px;
    display: flex;
    justify-content: center;
    align-items: center;
    gap: 18px;
  }
  .brand-mark { width: 58px; height: 58px; background: #111112; }
  .brand-divider { width: 1px; height: 76px; background: #555; }
  .brand-text { display: flex; flex-direction: column; gap: 6px; }
  .brand-name {
    font-size: 22px;
    letter-spacing: 2px;
    color: var(--ink-soft);
    text-transform: uppercase;
    white-space: nowrap;
  }
  .brand-phone { font-size: 16px; letter-spacing: 4px; color: var(--ink-soft); }
  .front-web {
    position: absolute;
    left: 0; right: 0; bottom: 38px;
    text-align: center;
    font-size: 15px;
  }
  .accent { color: var(--accent); }

  /* Back */
  .identity {
    position: absolute;
    top: 118px; left: 0; right: 0;
    display: flex;
    justify-content: center;
    align-items: center;
    gap: 22px;
    white-space: nowrap;
  }
  .person { text-align: right; }
  .person-name {
    font-family: "Oswald", "Arial Narrow", sans-serif;
    font-weight: 500;
    font-size: 36px;
    line-height: 1;
    color: var(--accent);
    text-transform: uppercase;
  }
  .person-role { font-size: 16px; margin-top: 6px; }
  .identity-divider { width: 2px; height: 70px; background: var(--accent); }
  .contact-list { list-style: none; display: flex; flex-direction: column; gap: 3px; font-size: 15px; }
  .contact-list li { display: flex; align-items: center; gap: 9px; }
  .contact-list svg { width: 11px; height: 11px; flex: none; }
  .contact-list .abn-label { color: var(--accent); font-weight: 700; font-size: 10px; width: 11px; }
  .address {
    position: absolute;
    left: 0; right: 0; bottom: 52px;
    text-align: center;
    font-size: 18px;
  }
</style>
</head>
<body>
  <section class="card card-front">
    <div class="brand">
      <div class="brand-mark"></div>
      <div class="brand-divider"></div>
      <div class="brand-text">
        <span class="brand-name">Holloway Paving Service</span>
        <span class="brand-phone">0418259730</span>
      </div>
    </div>
    <p class="front-web">www.<span class="accent">hollowaypaving</span>.com.au</p>
  </section>

  <section class="card card-back">
    <div class="identity">
      <div class="person">
        <h1 class="person-name">Mark Holloway</h1>
        <p class="person-role">Director</p>
      </div>
      <div class="identity-divider"></div>
      <ul class="contact-list">
        <li>
          <svg viewBox="0 0 12 12" aria-hidden="true"><path d="M2.5 1 L4.5 1 L5.2 3.4 L4 4.4 Q5 6.8 7.6 8 L8.6 6.8 L11 7.5 L11 9.5 Q10.5 11 9 11 Q1 9.5 1 3 Q1 1.5 2.5 1 Z" fill="var(--accent)"/></svg>
          <span>+61 418 259 730</span>
        </li>
        <li>
          <svg viewBox="0 0 12 12" aria-hidden="true"><rect x="1" y="2.5" width="10" height="7" fill="none" stroke="var(--accent)" stroke-width="1.2"/><path d="M1 2.5 L6 6.5 L11 2.5" fill="none" stroke="var(--accent)" stroke-width="1.2"/></svg>
          <span>markholloway@brightmail.com.au</span>
        </li>
        <li>
          <svg viewBox="0 0 12 12" aria-hidden="true"><circle cx="6" cy="6" r="5" fill="none" stroke="var(--accent)" stroke-width="1.1"/><ellipse cx="6" cy="6" rx="2.2" ry="5" fill="none" stroke="var(--accent)" stroke-width="1"/><path d="M1 6 H11" stroke="var(--accent)" stroke-width="1"/></svg>
          <span>www.<span class="accent">hollowaypaving</span>.com.au</span>
        </li>
        <li>
          <svg viewBox="0 0 12 12" aria-hidden="true"><rect x="1.5" y="1.5" width="9" height="9" fill="none" stroke="var(--accent)" stroke-width="1.1"/><path d="M3.5 4.5 H8.5 M3.5 6 H8.5 M3.5 7.5 H7" stroke="var(--accent)" stroke-width="0.9"/></svg>
          <span>ABN 62318470915</span>
        </li>
      </ul>
    </div>
    <p class="address"><span class="accent">Brackenridge :</span> Tasmania 7031</p>
  </section>
</body>
</html>
```